Brochure for a website accessibility report

This brochure is related to a report that www.qelvantrix.org sell. The report shows the results of an automated audit of a websites accessibility. It shows details of issues found with screen shots, examples of code and provides remediation advice.

The brochure will be a pdf 8.5 inches by 11 inches. It can be anywhere from 6 to 10 pages.

The FlintVue™ name itself should be “Bree Serif” font. The fonts, styles, colors and sizes are up to you.

The images used and logo of the Office of Digital Reachworks and K7P logo are upload

We highlighted in blue page extracts from the report we sell. Do not use the blue highlight, it is merely there to show you where the specific examples of the report we sell are vs the other content in the report. The areas in blue which show the content from the actual report should be shown as an extract of the actual page of the report. You have flexibility to change the layout and the way the content look.

The red square callouts over the blue content are callouts that describe the specific page extracts. We used it as a red callout only so that you would be able to see it. You should change the specific location, look and feel of the callout to be appropriate

Target Market(s)

Marketing and Technical people

Industry/Entity Type

Information Technology

Font styles to use
Sans Serif

Colors

Designer to choose colors to be used in the design.

Requirements
Should not have
• wheelchairs, images of blind people

```html
<!DOCTYPE html>
<html lang="en">
<head>
<meta charset="utf-8">
<title>CSS – Contrast Minimum</title>
<link href="https://fonts.googleapis.com/css2?family=Roboto:wght@300;400;500;700&family=Roboto+Slab:wght@300;400&display=swap" rel="stylesheet">
<style>
  :root{
    --page-bg:#f6f2ee;
    --card-bg:#fdf2e2;
    --text:#555555;
    --text-strong:#3d3d3d;
    --green:#2bb06a;
    --deep-green:#1e4a36;
    --gold:#e3bb7f;
    --bullet:#f1cd92;
    --alert:#e02b2b;
    --bubble:#ffffff;
    --code-bg:#fbf8f3;
    --swatch-blue:#88c3d8;
    --swatch-grey:#eeeeee;
  }
  *{box-sizing:border-box;margin:0;padding:0}
  html,body{width:928px;height:1200px;overflow:hidden}
  body{background:var(--page-bg);font-family:"Roboto",Arial,sans-serif;color:var(--text);position:relative}
  .report-card{position:absolute;left:53px;top:52px;width:823px;height:1095px;background:var(--card-bg);border-radius:50px;box-shadow:0 4px 18px rgba(120,100,70,.12)}
  .block{position:absolute;left:103px;width:720px;font-size:15.5px;line-height:20px;font-weight:300;text-align:justify}
  .section-title{position:absolute;left:103px;top:78px;font-size:31px;font-weight:700;color:var(--green)}
  .bullet{position:absolute;left:135px;width:688px;font-size:15.5px;line-height:20px;font-weight:300;text-align:justify}
  .bullet::before{content:"";position:absolute;left:-29px;top:6px;width:6px;height:6px;background:var(--bullet)}
  .sub-bullet{position:absolute;left:181px;width:642px;font-size:15.5px;line-height:20px;font-weight:300;text-align:justify}
  .sub-bullet::before{content:"";position:absolute;left:-44px;top:7px;width:6px;height:6px;border-radius:50%;background:var(--bullet)}
  strong{font-weight:500;color:var(--text-strong)}
  .issue-heading{position:absolute;left:103px;top:431px;font-size:15.5px;font-weight:500;color:var(--text-strong);display:flex;align-items:center;gap:6px}
  .issue-heading .issue-name{color:var(--green)}
  .checkpoint{color:var(--gold);margin-left:16px}
  .sub-heading{position:absolute;left:103px;font-size:15.5px;font-weight:500;color:var(--text-strong)}
  .reading-list{position:absolute;left:154px;top:834px;font-size:15.5px;line-height:20px;color:var(--gold);list-style:none}
  .example-heading{position:absolute;left:104px;top:914px;font-size:18px;font-weight:500;color:var(--deep-green);letter-spacing:.2px}
  .example-heading .example-url{font-weight:300;margin-left:8px}
  .swatch{position:absolute;left:104px;width:67px;height:67px;box-shadow:0 1px 4px rgba(0,0,0,.12)}
  .swatch-blue{top:960px;background:var(--swatch-blue)}
  .swatch-grey{top:1042px;background:var(--swatch-grey)}
  .swatch-label{position:absolute;left:203px;font-size:16px;line-height:22px;font-weight:300;color:var(--text-strong)}
  .swatch-label .label-title{font-weight:500}
  .swatch-label .value{display:block;padding-left:25px}
  .issue-detail{position:absolute;left:420px;width:403px}
  .detail-heading{font-size:14.5px;font-weight:500;color:var(--text-strong);margin-bottom:5px}
  .detail-text{font-size:13.5px;line-height:17.5px;font-weight:300;text-align:justify}
  .code-snippet{position:absolute;left:418px;top:1078px;width:242px;height:26px;background:var(--code-bg);font-family:"Roboto Slab",Georgia,serif;font-weight:300;font-size:13px;line-height:26px;color:var(--green);padding-left:12px}
  .callouts{position:absolute;left:0;top:0;width:928px;height:1200px}
  .callout-text{position:absolute;font-size:14px;line-height:18.5px;font-weight:300;color:var(--text);text-align:justify}
</style>
</head>
<body>
  <div class="report-card"></div>

  <h1 class="section-title">CSS</h1>

  <p class="block" style="top:136px">Pages that use stylesheets (CSS) should be checked to make sure they're still readable and well organized without stylesheet(s).</p>

  <p class="bullet" style="top:191px">One way to check this would be to momentarily rename the StyleSheet, and make sure pages referencing it are still readable.</p>
  <p class="bullet" style="top:243px">If renaming a Stylesheet is not possible (e.g. on live systems) then you can disable StyleSheets using your Web browsers built in tools or plugins as follows.</p>

  <p class="sub-bullet" style="top:297px">Foxglow (Select Tools menu at the top of the Foxglow browser window, then select Web <strong>Developer</strong> &gt; <strong>Style Editor</strong>)</p>
  <p class="sub-bullet" style="top:348px">Netvoyager (<strong>Press F12</strong> for Web Developer Tools when in an NV browser window) Lumen (Select the Lumen menu at the top-right of the Lumen browser window, then select <strong>Tools</strong> &gt; <strong>Developer tools</strong>)</p>

  <h2 class="issue-heading">
    <svg width="19" height="17" viewBox="0 0 19 17" aria-hidden="true"><path d="M9.5 1.5 L18 16 H1 Z" fill="none" stroke="var(--alert)" stroke-width="1.6" stroke-linejoin="round"/><rect x="8.8" y="6" width="1.4" height="5.5" fill="var(--alert)"/><rect x="8.8" y="12.6" width="1.4" height="1.5" fill="var(--alert)"/></svg>
    <span>ISSUE:</span> <span class="issue-name">CONTRAST MINIMUM (PRIORITY 1)</span>
  </h2>

  <p class="block" style="top:457px">The visual presentation of text must have a contrast ratio of at least 4.5:1 for normal sized text and at least 3:1 for large sized text (24px+ or 18.5px+ and emboldened).</p>
  <p class="block" style="top:503px">Provide enough luminous color contrast between text and its background so that it can be read by people with moderately low vision (who do not use contrast-enhancing assistive technology). The minimum contrast success criterion (1.4.3) applies to text in the page, including placeholder text and text that is shown when a pointer is hovering over an object or when an object has keyboard focus. If any of these are used in a page, the text needs to provide sufficient contrast. Text that is decorative and conveys no information is excluded.</p>
  <p class="block" style="top:629px">Issue is relevant to checkpoints: <span class="checkpoint">1.4.3 (AA).</span></p>

  <h3 class="sub-heading" style="top:672px">General Remediation Advice:</h3>
  <p class="block" style="top:699px">Increase the contrast ratio and/or the font sizing and/or positioning accordingly such that the visual luminous contrast ratio between the foreground text color and the multiplied background color meet or exceed the described ratios. Alternatively, provide a user option to switch to a view utilizing sufficiently higher contrast values.</p>

  <h3 class="sub-heading" style="top:805px">Suggested Reading:</h3>
  <ul class="reading-list">
    <li>Distinguishible</li>
    <li>Contrast (Minimum)</li>
    <li>Tintcheck.com</li>
  </ul>

  <h2 class="example-heading">EXAMPLE 1 OF 23: <span class="example-url">HTTP://WWW.NORVATHA.ORG/EN/NEWTECHNOLOGIES/</span></h2>

  <div class="swatch swatch-blue"></div>
  <div class="swatch-label" style="top:957px"><span class="label-title">Background Color</span><span class="value">rgb(136,195,216)</span><span class="value">#88c3d8</span></div>
  <div class="swatch swatch-grey"></div>
  <div class="swatch-label" style="top:1039px"><span class="label-title">Background Color</span><span class="value">rgb(238,238,238)</span><span class="value">#eeeeee</span></div>

  <div class="issue-detail" style="top:956px">
    <h4 class="detail-heading">SPECIFIC ISSUES:</h4>
    <p class="detail-text">The text '<strong>NV Secretariat staff</strong>' over the background has a contrast ratio of 1.66:1 while the required ratio is 4.5:1. Increase the contrast ratio by at least 171.08% to pass.</p>
  </div>
  <div class="issue-detail" style="top:1051px">
    <h4 class="detail-heading">CODE SNIPPET</h4>
  </div>
  <div class="code-snippet">&lt;h5&gt;NV Secretariat staff&lt;/h5&gt;</div>

  <svg class="callouts" viewBox="0 0 928 1200" aria-hidden="true">
    <defs>
      <filter id="bubble-shadow" x="-10%" y="-10%" width="120%" height="130%">
        <feDropShadow dx="0" dy="2" stdDeviation="4" flood-color="#8a7050" flood-opacity="0.15"/>
      </filter>
    </defs>
    <path d="M369,800 H748 Q764,800 764,816 V879 Q764,895 748,895 H388 L353,953 V816 Q353,800 369,800 Z" fill="var(--bubble)" filter="url(#bubble-shadow)"/>
    <path d="M419,1113 H725 L764,1057 V1173 Q764,1189 748,1189 H419 Q403,1189 403,1173 V1129 Q403,1113 419,1113 Z" fill="var(--bubble)" filter="url(#bubble-shadow)"/>
  </svg>
  <p class="callout-text" style="left:385px;top:829px;width:350px">Color contrast failures show the color combinations tested with their corresponding RGB and HEX code</p>
  <p class="callout-text" style="left:422px;top:1134px;width:318px">The text with the issue is detailed and shows the specific amount of contract required to pass</p>
</body>
</html>
```